Larvik GmbH needs a sensational homepage!

A draft of the performances and the logo were uploaded in the attachment. The homepage should be adapted to the colors of the logo. Either pictures, graphics or icons of the respective topic are to be used for the buttons. Social media Network, Video, Photos should not be missing. An imprint, contact form with telephone number and email address should be given on the home page. The page should definitely be designed to be responsive for all end devices. Texts as well as images and videos are inserted in the sub-menus or pages. Only the structure and a simple application should be given. We have already secured the domain www.larvik-demo.at.
We are a young, dynamic company with a high technical affinity. Ask for creative suggestions. If something is needed, please contact us.

Target Market(s)

Construction industry, client

Requirements
Must have
• see description
Should not have
• shouldn't be colorful and playful

```html
<!DOCTYPE html>
<html lang="en">
<head>
<meta charset="utf-8">
<title>Larvik GmbH</title>
<link rel="stylesheet" href="https://fonts.googleapis.com/css2?family=Cinzel:wght@400;500&family=Lato:wght@400;700&display=swap">
<style>
  :root {
    --ink: #1c1c1c;
    --slate: #24353e;
    --slate-deep: #141e25;
    --slate-mid: #2c3f49;
    --grey: #8f9196;
    --ring: #9a9b9f;
    --muted: #5d5d5d;
    --white: #ffffff;
    --nav-dim: #a7adb1;
  }
  * { box-sizing: border-box; margin: 0; padding: 0; }
  html, body { width: 771px; height: 1200px; overflow: hidden; }
  body { position: relative; background: var(--white); font-family: "Lato", sans-serif; color: var(--ink); }

  .hero { position: absolute; left: 0; top: 0; width: 771px; height: 460px; }
  .hero-photo { position: absolute; inset: 0; background: linear-gradient(160deg, #2a3941 0%, #1b262d 45%, #3a474f 100%); }

  .brand { position: absolute; left: 93px; top: 30px; font-family: "Cinzel", serif; font-size: 24px; letter-spacing: 4px; color: var(--white); line-height: 1; }
  .brand-sub { display: block; }
  .nav { position: absolute; top: 38px; left: 346px; display: flex; gap: 21px; font-size: 11px; color: var(--white); align-items: center; }
  .nav .current { color: var(--nav-dim); }
  .nav .login { font-weight: 700; display: flex; align-items: center; gap: 4px; margin-left: 0; }
  .cta { position: absolute; left: 590px; top: 35px; width: 89px; height: 25px; background: var(--grey); color: var(--white); font-size: 10px; font-weight: 700; display: flex; align-items: center; justify-content: center; }

  .hero-title { position: absolute; left: 0; width: 771px; top: 182px; text-align: center; font-family: "Cinzel", serif; font-size: 52px; letter-spacing: 14px; color: var(--white); font-weight: 400; padding-left: 14px; }
  .hero-tagline { position: absolute; left: 0; width: 771px; top: 268px; text-align: center; font-size: 14.5px; color: var(--white); }
  .hero-social { position: absolute; left: 0; width: 771px; top: 330px; display: flex; justify-content: center; gap: 24px; font-size: 11px; font-weight: 700; color: var(--white); letter-spacing: .5px; }

  .services-title { position: absolute; left: 0; width: 771px; top: 512px; text-align: center; font-family: "Cinzel", serif; font-size: 31px; letter-spacing: 3px; font-weight: 400; }
  .service { position: absolute; top: 599px; width: 170px; text-align: center; }
  .service-badge { display: block; margin: 0 auto; }
  .service-name { margin-top: 18px; font-size: 14px; font-weight: 700; line-height: 17px; }
  .service-text { margin-top: 8px; font-size: 8.6px; line-height: 15px; color: var(--muted); }

  .footer { position: absolute; left: 0; top: 893px; width: 771px; height: 307px; color: var(--white); }
  .footer-photo { position: absolute; inset: 0; background: linear-gradient(180deg, var(--slate-mid) 0%, #26363f 60%, #2d3f48 100%); }
  .footer-heading { position: absolute; top: 50px; font-family: "Cinzel", serif; font-size: 29px; font-weight: 400; letter-spacing: 1.5px; }
  .visit { left: 117px; }
  .contact { left: 365px; }
  .address { position: absolute; left: 117px; top: 113px; font-size: 8.6px; line-height: 15px; }
  .phone { position: absolute; left: 116px; top: 149px; font-size: 8.6px; }
  .footer-social { position: absolute; left: 116px; top: 186px; display: flex; gap: 16px; font-size: 9px; font-weight: 700; }

  .form { position: absolute; left: 367px; top: 111px; width: 287px; }
  .form-row { display: flex; height: 27px; border: 1px solid var(--ring); border-bottom: none; }
  .field { flex: 1; font-size: 7.5px; padding: 8px 15px; }
  .field + .field { border-left: 1px solid var(--ring); }
  .message { height: 53px; border: 1px solid var(--ring); font-size: 7.5px; padding: 8px 15px; }
  .submit { height: 27px; background: var(--grey); font-size: 9px; font-weight: 700; display: flex; align-items: center; justify-content: center; }

  .legal { position: absolute; left: 0; width: 771px; top: 265px; text-align: center; font-size: 8.6px; }
</style>
</head>
<body>
  <header class="hero">
    <div class="hero-photo" role="img" aria-label="Scaffolding frames against a dark cloudy sky"></div>
    <div class="brand">LARVIK<span class="brand-sub" style="font-size:9px;letter-spacing:2px;text-align:right;margin-top:4px;">GMBH</span></div>
    <nav class="nav">
      <span class="current">Home</span>
      <span>Services</span>
      <span>Contact</span>
      <span class="login">
        <svg width="8" height="9" viewBox="0 0 8 9"><circle cx="4" cy="2.3" r="2.2" fill="#fff"/><path d="M0 9 C0 5.5 8 5.5 8 9Z" fill="#fff"/></svg>LOGIN</span>
    </nav>
    <div class="cta">GET STARTED</div>
    <h1 class="hero-title">LARVIKGMBH</h1>
    <p class="hero-tagline">Lorem ipsum dolor sit amet consectetur adipiscing elit</p>
    <div class="hero-social"><span>Network</span><span>Video</span><span>Photos</span></div>
  </header>

  <h2 class="services-title">OUR SERVICES</h2>

  <section class="service" style="left:86px;">
    <svg class="service-badge" width="134" height="134" viewBox="0 0 134 134">
      <circle cx="67" cy="67" r="65.5" fill="none" stroke="#24353e" stroke-width="2.2"/>
      <circle cx="67" cy="67" r="54" fill="none" stroke="#9a9b9f" stroke-width="4"/>
      <rect x="42" y="42" width="50" height="50" fill="#e6e8e9" role="img" aria-label="Scaffolding icon"/>
    </svg>
    <h3 class="service-name">Scaffolding</h3>
    <p class="service-text">Lorem ipsum dolor sit aonsectdipiscing elit, sed do eiusmod tempor incididunt ut labore et dolore mauis ipsum suspendisse ultrices gravisus commodo viverra</p>
  </section>

  <section class="service" style="left:300px;">
    <svg class="service-badge" width="134" height="134" viewBox="0 0 134 134">
      <circle cx="67" cy="67" r="65.5" fill="none" stroke="#24353e" stroke-width="2.2"/>
      <circle cx="67" cy="67" r="54" fill="none" stroke="#9a9b9f" stroke-width="4"/>
      <rect x="42" y="42" width="50" height="50" fill="#e6e8e9" role="img" aria-label="Blueprint and gear icon"/>
    </svg>
    <h3 class="service-name">Redevelopment<br>Project management</h3>
    <p class="service-text">Lorem ipsum dolor sit aonsectdipiscing elit, sed do eiusmod tempor incididunt ut ultrices gravisus commodo viverra</p>
  </section>

  <section class="service" style="left:514px;">
    <svg class="service-badge" width="134" height="134" viewBox="0 0 134 134">
      <circle cx="67" cy="67" r="65.5" fill="none" stroke="#24353e" stroke-width="2.2"/>
      <circle cx="67" cy="67" r="54" fill="none" stroke="#9a9b9f" stroke-width="4"/>
      <rect x="42" y="42" width="50" height="50" fill="#e6e8e9" role="img" aria-label="Insulation roll icon"/>
    </svg>
    <h3 class="service-name">Screed &amp; insulation</h3>
    <p class="service-text">Lorem ipsum dolor sit aonsectdipiscing elit, sed do eiusmod tempor incididunt ut labore et dolore mauis ipsum suspendisse ultrices gravisus commodo viverra</p>
  </section>

  <footer class="footer">
    <div class="footer-photo" role="img" aria-label="Faint photo of workers on scaffolding"></div>
    <h2 class="footer-heading visit">Visit Us</h2>
    <p class="address">1233,Lorem ipsum dolor sit ametmod tempo<br>incididunt onsectetur adipiscing elit</p>
    <p class="phone">Phone : 1 555 010 2040</p>
    <div class="footer-social"><span>Network</span><span>Video</span><span>Photos</span></div>

    <h2 class="footer-heading contact">Contact Us</h2>
    <form class="form">
      <div class="form-row"><div class="field">Telephone number</div><div class="field">Email address</div></div>
      <div class="message">Message</div>
      <div class="submit">SUBMIT MESSAGE</div>
    </form>

    <p class="legal">© 2021 Larvik.All Rights Reserved &nbsp;|&nbsp; Privacy Policy &nbsp;|&nbsp; Terms and Use &nbsp;|&nbsp; Imprint</p>
  </footer>
</body>
</html>
```